Business Card & Letterhead Design

We a financial advice company based in Australia. We provide advice to wealthy farmers.

We are changing our business name FROM Brightvale Financial TO Tallowmere Wealth and we need a new letterhead and double sided business card design

Attached is designs from our previous branding (Brightvale Financial) as it includes all the details we require on the new Tallowmere Wealth business cards and letterhead.

Need extra days to review

```html
<!DOCTYPE html>
<html lang="en">
<head>
<meta charset="utf-8">
<title>Tallowmere Wealth – Business Card</title>
<link rel="stylesheet" href="https://fonts.googleapis.com/css2?family=Cinzel:wght@400;500&family=Montserrat:wght@400;500&display=swap">
<style>
  :root{
    --backdrop:#2a2a2a;
    --slate:#5b676d;
    --charcoal:#434343;
    --accent:#7f909a;
    --paper:#ffffff;
    --ink:#3a3a3a;
    --muted:#8a959b;
    --light:#f2f4f5;
  }
  *{margin:0;padding:0;box-sizing:border-box}
  html,body{width:1200px;height:900px;overflow:hidden;background:var(--backdrop)}
  .canvas{position:relative;width:1200px;height:900px}
  .card{position:absolute;width:560px;height:340px;border-radius:22px;overflow:hidden}

  /* front */
  .card-front{left:50px;top:90px;background:var(--slate);color:var(--light)}
  .front-wordmark{position:absolute;left:44px;top:92px}
  .wordmark-name{font-family:"Cinzel",serif;font-size:25px;letter-spacing:1px;line-height:1;white-space:nowrap}
  .wordmark-sub{font-family:"Montserrat",sans-serif;font-size:8.5px;letter-spacing:4.2px;margin-top:3px;opacity:.85;white-space:nowrap}
  .services{position:absolute;left:44px;top:150px;list-style:none}
  .services li{font-family:"Cinzel",serif;font-size:16px;letter-spacing:.5px;display:flex;align-items:center;gap:10px;margin-bottom:6px}
  .services li svg{flex:none}
  .licensee{position:absolute;left:44px;top:272px;font-family:"Montserrat",sans-serif;font-size:12.5px;line-height:1.5;letter-spacing:.3px}
  .front-mark{position:absolute;right:46px;top:40px;width:160px;height:160px;border:4px solid var(--light);border-radius:50%;display:flex;align-items:center;justify-content:center;text-align:center;font-family:"Cinzel",serif;font-size:19px;line-height:1.25;color:var(--light)}

  /* back */
  .card-back{left:590px;top:470px;background:var(--paper);color:var(--ink)}
  .back-shape{position:absolute;inset:0}
  .back-brand{position:absolute;left:40px;top:40px}
  .brand-dot{display:block;width:44px;height:44px;border:2.5px solid var(--ink);border-radius:50%;margin:0 0 10px 70px}
  .back-brand .wordmark-name{font-size:17px;color:var(--ink)}
  .back-brand .wordmark-sub{font-size:6.5px;letter-spacing:2.9px;color:var(--muted)}
  .person{position:absolute;left:40px;top:166px}
  .person-name{font-family:"Cinzel",serif;font-size:15px;color:var(--accent);white-space:nowrap}
  .person-name .creds{font-family:"Montserrat",sans-serif;font-size:10.5px;color:var(--ink)}
  .person-role{font-family:"Montserrat",sans-serif;font-size:12px;line-height:1.4;margin-top:3px}
  .tagline{position:absolute;left:40px;top:278px;font-family:"Cinzel",serif;font-size:14px;letter-spacing:.6px}
  .contact{position:absolute;right:26px;top:30px;text-align:right;color:var(--light);font-family:"Montserrat",sans-serif;font-size:11px;line-height:1.62;white-space:nowrap}
  .contact .motto{font-family:"Cinzel",serif;font-size:11px}
  .contact-row{display:flex;justify-content:flex-end;align-items:center;gap:6px}
</style>
</head>
<body>
<div class="canvas">

  <section class="card card-front">
    <div class="front-wordmark">
      <div class="wordmark-name">TALLOWMERE WEALTH</div>
      <div class="wordmark-sub">STRATEGIC FINANCIAL ADVICE</div>
    </div>
    <ul class="services">
      <li><svg width="14" height="14"><circle cx="7" cy="7" r="6" fill="none" stroke="#f2f4f5" stroke-width="1.2"/><rect x="4" y="7" width="1.5" height="3" fill="#f2f4f5"/><rect x="6.3" y="5" width="1.5" height="5" fill="#f2f4f5"/><rect x="8.6" y="6" width="1.5" height="4" fill="#f2f4f5"/></svg>LIFE &amp; TPD INSURANCE</li>
      <li><svg width="14" height="14"><circle cx="7" cy="7" r="6" fill="none" stroke="#f2f4f5" stroke-width="1.2"/><rect x="4" y="7" width="1.5" height="3" fill="#f2f4f5"/><rect x="6.3" y="5" width="1.5" height="5" fill="#f2f4f5"/><rect x="8.6" y="6" width="1.5" height="4" fill="#f2f4f5"/></svg>INCOME PROTECTION</li>
      <li><svg width="14" height="14"><circle cx="7" cy="7" r="6" fill="none" stroke="#f2f4f5" stroke-width="1.2"/><rect x="4" y="7" width="1.5" height="3" fill="#f2f4f5"/><rect x="6.3" y="5" width="1.5" height="5" fill="#f2f4f5"/><rect x="8.6" y="6" width="1.5" height="4" fill="#f2f4f5"/></svg>FINANCIAL PLANNING</li>
      <li><svg width="14" height="14"><circle cx="7" cy="7" r="6" fill="none" stroke="#f2f4f5" stroke-width="1.2"/><rect x="4" y="7" width="1.5" height="3" fill="#f2f4f5"/><rect x="6.3" y="5" width="1.5" height="5" fill="#f2f4f5"/><rect x="8.6" y="6" width="1.5" height="4" fill="#f2f4f5"/></svg>RETIREMENT PLANNING</li>
    </ul>
    <p class="licensee">Harbourline Advisory Limited<br>Australian Financial Services Licensee-License Number 500112</p>
    <div class="front-mark">Tallowmere<br>Wealth</div>
  </section>

  <section class="card card-back">
    <svg class="back-shape" width="560" height="340" viewBox="0 0 560 340" aria-hidden="true">
      <circle cx="648" cy="94" r="378" fill="none" stroke="var(--accent)" stroke-width="5"/>
      <circle cx="660" cy="90" r="370" fill="var(--charcoal)"/>
    </svg>
    <div class="back-brand">
      <span class="brand-dot"></span>
      <div class="wordmark-name">TALLOWMERE WEALTH</div>
      <div class="wordmark-sub">STRATEGIC FINANCIAL ADVICE</div>
    </div>
    <div class="person">
      <div class="person-name">SAM REID <span class="creds">| B.Ag.Ec. Dip F.P. CFP®</span></div>
      <div class="person-role">Managing Director<br>Authorised Representative</div>
    </div>
    <div class="tagline">A REFERRAL BUILT BUSINESS</div>
    <div class="contact">
      <div class="motto">'FINANCIAL PEACE OF MIND'</div>
      <div class="contact-row">0400 555 182 <svg width="9" height="11"><rect x="1.5" y=".5" width="6" height="10" rx="1.2" fill="none" stroke="#f2f4f5"/></svg></div>
      <div class="contact-row">(07) 3100 5521 <svg width="11" height="10"><path d="M1 4c2-3 7-3 9 0l-2 1-1-1H4L3 5z" fill="#f2f4f5"/><rect x="3" y="5" width="5" height="4" fill="#f2f4f5"/></svg></div>
      <div class="contact-row">(07) 3100 5522 <svg width="11" height="10"><rect x="1" y="1" width="9" height="8" rx="1" fill="#f2f4f5"/></svg></div>
      <div class="contact-row">sam@tallowmerewealth.com.au <svg width="11" height="9"><rect x=".5" y=".5" width="10" height="8" fill="none" stroke="#f2f4f5"/><path d="M.5 .5l5 4 5-4" fill="none" stroke="#f2f4f5"/></svg></div>
      <div class="contact-row">www.tallowmerewealth.com.au <svg width="11" height="11"><circle cx="5.5" cy="5.5" r="4.8" fill="none" stroke="#f2f4f5"/><path d="M.7 5.5h9.6M5.5 .7v9.6" stroke="#f2f4f5"/></svg></div>
      <div class="motto">'FINANCIAL PEACE OF MIND'</div>
      <div>Suite 4, 18 Marlow St</div>
      <div>Riverbend, QLD 4000</div>
      <div>PO Box 1234, Eastfield</div>
    </div>
  </section>

</div>
</body>
</html>
```